Corvane Holdings , new business card design

investment firm with corporate clients . need double sided business card , vertical and horizontal options ,logo must be clear. prefer pantone colors only and sharp design. website also www.corvane.ae

Khalid Bin Tarrafi
Managing Director
Tel. +971 4 387 2940
Mobile +971 50 518 2403
khalid@corvane.ae
Q-Span Plaza, officw 18-B07, Warqa Gardens, Dubai

Contact Information for Business Card

Khalid Bin Tarrafi
Managing Director

Font styles to use
Serif

Colors

Designer to choose colors to be used in the design.

```html
<!DOCTYPE html>
<html lang="en">
<head>
<meta charset="utf-8">
<title>Corvane Holdings — Business Card</title>
<link rel="stylesheet" href="https://fonts.googleapis.com/css2?family=Questrial&display=swap">
<style>
  :root {
    --backdrop: #e6e3df;
    --brand-blue: #4a7299;
    --ink-dark: #3a3a3a;
    --ink-muted: #666a70;
    --rule-grey: #9a9a9a;
    --band-grey: #c9c7c3;
    --paper: #ffffff;
  }
  * { margin: 0; padding: 0; box-sizing: border-box; }
  html, body {
    width: 1200px;
    height: 997px;
    overflow: hidden;
    background: var(--backdrop);
    font-family: "Questrial", "Century Gothic", sans-serif;
  }
  .card-set {
    position: absolute;
    inset: 0;
    display: flex;
    align-items: center;
    justify-content: center;
    gap: 40px;
  }
  .card {
    position: relative;
    width: 540px;
    height: 308px;
    box-shadow: 0 6px 18px rgba(0,0,0,0.12);
    overflow: hidden;
  }

  /* Front side */
  .card--front {
    background: var(--brand-blue);
    display: flex;
    align-items: center;
    justify-content: center;
  }
  .wordmark {
    font-size: 34px;
    letter-spacing: 0.18em;
    text-transform: uppercase;
    white-space: nowrap;
  }
  .card--front .wordmark { color: var(--paper); }

  /* Back side */
  .card--back { background: var(--paper); }
  .card--back .wordmark {
    position: absolute;
    top: 34px;
    right: 36px;
    font-size: 24px;
    color: var(--brand-blue);
  }
  .divider {
    position: absolute;
    top: 84px;
    left: 36px;
    right: 36px;
    height: 1px;
    background: var(--rule-grey);
  }
  .holder {
    position: absolute;
    left: 36px;
    top: 150px;
  }
  .holder-name {
    font-size: 17px;
    font-weight: 700;
    color: var(--brand-blue);
    letter-spacing: 0.02em;
    text-transform: uppercase;
  }
  .holder-title {
    font-size: 15px;
    color: var(--ink-muted);
    margin-top: 2px;
    padding-bottom: 10px;
    border-bottom: 1px solid var(--rule-grey);
    width: 150px;
  }
  .contact-list {
    list-style: none;
    margin-top: 8px;
  }
  .contact-list li {
    display: flex;
    align-items: center;
    gap: 8px;
    font-size: 15px;
    color: var(--ink-dark);
    line-height: 21px;
  }
  .contact-list svg { width: 12px; height: 12px; fill: var(--brand-blue); }
  .office-address {
    position: absolute;
    right: 36px;
    top: 160px;
    text-align: right;
    font-size: 15px;
    line-height: 21px;
    color: var(--ink-dark);
  }
  .edge-band {
    position: absolute;
    left: 0;
    right: 0;
    bottom: 0;
    height: 12px;
    background: var(--brand-blue);
  }
  .edge-band::before {
    content: "";
    position: absolute;
    left: 0;
    right: 0;
    top: -6px;
    height: 6px;
    background: var(--band-grey);
  }
</style>
</head>
<body>
  <main class="card-set">
    <section class="card card--front" aria-label="Card front">
      <div class="wordmark">Corvane Holdings</div>
    </section>

    <section class="card card--back" aria-label="Card back">
      <div class="wordmark">Corvane Holdings</div>
      <div class="divider"></div>

      <div class="holder">
        <div class="holder-name">Khalid Bin Tarrafi</div>
        <div class="holder-title">Managing Director</div>
        <ul class="contact-list">
          <li>
            <svg viewBox="0 0 24 24" aria-hidden="true"><path d="M6.6 10.8a15.2 15.2 0 0 0 6.6 6.6l2.2-2.2a1 1 0 0 1 1-.25 11.4 11.4 0 0 0 3.6.57 1 1 0 0 1 1 1V20a1 1 0 0 1-1 1A17 17 0 0 1 3 4a1 1 0 0 1 1-1h3.5a1 1 0 0 1 1 1c0 1.25.2 2.45.57 3.57a1 1 0 0 1-.25 1z"/></svg>
            +971 4 387 2940
          </li>
          <li>
            <svg viewBox="0 0 24 24" aria-hidden="true"><path d="M7 1h10a2 2 0 0 1 2 2v18a2 2 0 0 1-2 2H7a2 2 0 0 1-2-2V3a2 2 0 0 1 2-2zm0 3v14h10V4zm5 15.5a1.2 1.2 0 1 0 0 2.4 1.2 1.2 0 0 0 0-2.4z"/></svg>
            +971 50 518 2403
          </li>
          <li>
            <svg viewBox="0 0 24 24" aria-hidden="true"><path d="M2 5h20v14H2zm2 2v.5l8 5 8-5V7l-8 5z"/></svg>
            khalid@corvane.ae
          </li>
        </ul>
      </div>

      <address class="office-address" style="font-style:normal">
        Q-Span Plaza, officw 18-B07,<br>
        Warqa Gardens, Dubai
      </address>

      <div class="edge-band"></div>
    </section>
  </main>
</body>
</html>
```